Brisk Rainshield - Logo and Advert

Help to provide logo and advert.
Advert is to be short and concise to fit in a printed directory posted around homes.
Ideally the same advert to be able to be blown up as a leaflet.
Use of eco friendly type colours, soft greens and blues.
Logo to be subtle but indicative to roofing and facades.
Breakdown of advert as follows;
Company name:
Brisk Rainshield
Sub title:
Roofing & Façades
Services breakdown:
Pitched (Slating & Tiling)
Flat (Single Ply, Liquid & Mineral Felt)
Hard Metal (Zinc Standing Seam)
Leadwork
Roof lights and lanterns
Generic notes:
100% flame free applications available, eliminating all fire risks to your property. (No gas torch’s etc.).
Expert consultation and advice.
Product warranty and/or insurance backed warranty available.
Fully insured contractor.
Contact information:
Phone number to be confirmed
Email and/or website to be confirmed.
Please feel free to try out different colours and fonts other than outlined. I am not limited to those and open to suggestions.
Target Market(s)
Domestic/Private Home Owners/Small Buidlers
Industry/Entity Type
Roofing
Font styles to use
Look and feel
Each slider illustrates characteristics of the customer's brand and the style your logo design should communicate.

```html
<!DOCTYPE html>
<html lang="en">
<head>
<meta charset="utf-8">
<title>Brisk Rainshield – Roofing &amp; Façades Leaflet</title>
<link href="https://fonts.googleapis.com/css2?family=Oswald:wght@300;700&family=Questrial&family=Figtree:wght@400;600;800&display=swap" rel="stylesheet">
<style>
  :root {
    --backdrop: #acd3ea;
    --brand-blue: #2a8fd6;
    --brand-green: #a5cd3a;
    --green-soft: #d6e9a6;
    --sidebar-bg: #eef1f6;
    --ink: #333a40;
    --white: #ffffff;
  }
  * { box-sizing: border-box; margin: 0; padding: 0; }
  html, body { width: 1200px; height: 900px; overflow: hidden; }
  body {
    background: var(--backdrop);
    display: flex; align-items: center; justify-content: center;
    font-family: "Figtree", sans-serif;
    color: var(--ink);
  }
  .leaflet {
    position: relative;
    width: 640px; height: 860px;
    background: var(--white);
    display: grid;
    grid-template-columns: 424px 216px;
    grid-template-rows: 1fr 44px;
    box-shadow: 0 10px 28px rgba(30, 80, 120, .25);
  }
  .main-column { padding: 18px 0 14px 18px; display: flex; flex-direction: column; }

  .brand { text-align: center; padding-right: 8px; }
  .brand-name {
    font-family: "Questrial", sans-serif;
    font-size: 29px; letter-spacing: .5px; line-height: 1;
    color: var(--brand-blue); text-transform: uppercase;
  }
  .brand-tagline {
    display: flex; align-items: center; gap: 6px;
    font-family: "Questrial", sans-serif;
    font-size: 13px; color: var(--brand-green); text-transform: uppercase;
    margin-top: 3px;
  }
  .brand-tagline::before, .brand-tagline::after {
    content: ""; flex: 1; height: 1.5px; background: var(--brand-blue);
  }

  .hero { position: relative; margin-top: 12px; height: 414px; width: 398px; overflow: hidden; }
  .hero-photo {
    position: absolute; inset: 0;
    background: linear-gradient(180deg, #b8d7f1 0%, #c9def0 32%, #d8d3c6 45%, #cdc4b3 70%, #6fa04a 86%, #5c8f3a 100%);
  }
  .hero-headline {
    position: relative; padding: 40px 14px 0;
    font-family: "Oswald", sans-serif; color: var(--white);
    text-transform: uppercase; line-height: 1.02; text-align: center;
  }
  .hero-headline .line-light { display: block; font-weight: 300; font-size: 50px; letter-spacing: -.5px; }
  .hero-headline .line-bold { display: block; font-weight: 700; font-size: 50px; letter-spacing: -.5px; }

  .offer-panel {
    margin-top: 14px; width: 424px; margin-left: 0;
    border: 1.5px solid var(--green-soft); border-right: none;
    padding: 10px 0 12px 14px;
  }
  .offer-highlight {
    background: var(--brand-green); color: var(--white);
    padding: 14px 14px 16px 30px;
  }
  .offer-title { font-weight: 800; font-size: 34px; letter-spacing: -1px; line-height: 1.1; }
  .offer-text { font-size: 18px; line-height: 1.2; margin-top: 4px; }
  .benefits { list-style: none; margin: 20px 0 0 36px; }
  .benefits li {
    position: relative; padding-left: 24px;
    font-size: 18px; line-height: 1.2; margin-bottom: 10px;
  }
  .benefits li svg { position: absolute; left: 0; top: 5px; }

  .services {
    background: var(--sidebar-bg);
    padding: 18px 12px 0 6px;
    display: flex; flex-direction: column; gap: 10px;
  }
  .service { text-align: center; }
  .service-photo {
    height: 102px; border: 6px solid var(--brand-blue);
  }
  .service.is-green .service-photo { border-color: var(--brand-green); }
  .service-name { font-weight: 600; font-size: 17px; color: var(--brand-blue); margin-top: 8px; line-height: 1.05; letter-spacing: -.3px; }
  .service.is-green .service-name { color: var(--brand-green); }
  .service-detail { font-size: 10.5px; font-weight: 600; color: var(--brand-blue); letter-spacing: -.3px; }
  .service.is-green .service-detail { color: var(--brand-green); }

  .photo-metal { background: linear-gradient(170deg, #9aa0a3, #6f7579 60%, #8c9194); }
  .photo-pitched { background: linear-gradient(160deg, #cfd6dd, #6f7983 45%, #a4553f 100%); }
  .photo-lantern { background: linear-gradient(180deg, #5aa0d8 0%, #9cc7ea 40%, #4e5965 75%, #9a9ea2 100%); }
  .photo-flat { background: linear-gradient(135deg, #c9dbe8 0%, #5f90c9 45%, #3c6fb4 100%); }
  .photo-lead { background: linear-gradient(160deg, #b7bfc5, #6d7479 55%, #d9dde0); }

  .contact-bar {
    grid-column: 1 / -1;
    background: var(--brand-blue); color: var(--white);
    display: flex; align-items: center; justify-content: center; gap: 16px;
    font-weight: 600; font-size: 17px;
  }
  .contact-bar .divider { opacity: .9; }
</style>
</head>
<body>
  <article class="leaflet">
    <section class="main-column">
      <header class="brand">
        <div class="brand-name">Brisk Rainshield</div>
        <div class="brand-tagline">Roofing &amp; Façades</div>
      </header>

      <div class="hero">
        <div class="hero-photo" role="img" aria-label="Photograph of a detached brick family home with double garage, lawn and blue sky"></div>
        <h1 class="hero-headline">
          <span class="line-light">Thinking about your</span>
          <span class="line-bold">Home Impovment</span>
        </h1>
      </div>

      <div class="offer-panel">
        <div class="offer-highlight">
          <h2 class="offer-title">100% Flame Free</h2>
          <p class="offer-text">applications available, eliminating all fire risks to your property. (No gas torch’s etc).</p>
        </div>
        <ul class="benefits">
          <li><svg width="9" height="12" viewBox="0 0 9 12"><path d="M2 1l5 5-5 5" fill="none" stroke="#333a40" stroke-width="1.6"/></svg>Product warranty or insurance backed warranty available.</li>
          <li><svg width="9" height="12" viewBox="0 0 9 12"><path d="M2 1l5 5-5 5" fill="none" stroke="#333a40" stroke-width="1.6"/></svg>Expert consultation and advice.</li>
          <li><svg width="9" height="12" viewBox="0 0 9 12"><path d="M2 1l5 5-5 5" fill="none" stroke="#333a40" stroke-width="1.6"/></svg>Fully insured contractor.</li>
        </ul>
      </div>
    </section>

    <aside class="services">
      <div class="service">
        <div class="service-photo photo-metal" role="img" aria-label="Photograph of grey zinc standing seam cladding"></div>
        <div class="service-name">Hard Metal</div>
        <div class="service-detail">Zinc Standing seam</div>
      </div>
      <div class="service is-green">
        <div class="service-photo photo-pitched" role="img" aria-label="Photograph of a pitched tiled roof"></div>
        <div class="service-name">Pitched</div>
        <div class="service-detail">Slating and Tiling</div>
      </div>
      <div class="service">
        <div class="service-photo photo-lantern" role="img" aria-label="Photograph of a glass roof lantern on a flat roof"></div>
        <div class="service-name">Roof lights<br>and lanterns</div>
      </div>
      <div class="service is-green">
        <div class="service-photo photo-flat" role="img" aria-label="Photograph of a blue single ply membrane roll with water droplets"></div>
        <div class="service-name">Flat</div>
        <div class="service-detail">Single ply, Liquid and Mineral felt</div>
      </div>
      <div class="service">
        <div class="service-photo photo-lead" role="img" aria-label="Photograph of dressed leadwork on a roof edge"></div>
        <div class="service-name">Leadwork</div>
      </div>
    </aside>

    <footer class="contact-bar">
      <span>brisk-rainshield.example</span>
      <span class="divider">|</span>
      <span>hello@brisk-rainshield.example</span>
      <span class="divider">|</span>
      <span>0300 555 0199</span>
    </footer>
  </article>
</body>
</html>
```